Business Card Design for Varomir Facility Services

We are looking for a Business Card Design for the Company "Varomir Facility Services."
Front side:
- Company Logo (small)
- Company Name, address, pohone, website and personal data.
- white background, for text e.g. company colors (blue or green like in the logo)
Please use following data:
Company data:
Varomir Facility Services Kostelac
Birkenhaldweg 14
6330 Cham
www.varomir-fs.ch
Person data:
Tarik Kostelac
Geschäftsführer
+41 76 519 47 83
info@varomir-fs.ch
Back side:
could be colored in blue or green
please use a big logo sing and some smaller icons to say what is all beeing offered in facility services, like cleaning, maintenance cleaning
industrial cleaning, caretaking, gardening, disposal. There is no need for everyone of the icons if there are similar or an icon is standing for more of them.
colors to use:
blue: HEX 246BB0
green: HEX 52B33E

```html
<!DOCTYPE html>
<html lang="de">
<head>
<meta charset="utf-8">
<title>Varomir Facility Services – Visitenkarte</title>
<link href="https://fonts.googleapis.com/css2?family=Lato:wght@400;700&display=swap" rel="stylesheet">
<style>
  :root {
    --brand-blue: #246bb0;
    --brand-green: #52b33e;
    --text-grey: #5e5e5e;
    --card-white: #ffffff;
    --stage: #e8e5e1;
  }
  * { box-sizing: border-box; margin: 0; padding: 0; }
  html, body { width: 1200px; height: 848px; overflow: hidden; }
  body {
    background: var(--stage);
    font-family: "Lato", sans-serif;
    position: relative;
  }
  .card {
    position: absolute;
    background: var(--card-white);
    box-shadow: 0 4px 14px rgba(0,0,0,0.18);
  }
  .card--front { left: 251px; top: 28px; width: 672px; height: 380px; }
  .card--back  { left: 249px; top: 441px; width: 677px; height: 375px; }

  /* Brand name block */
  .brand { position: absolute; display: flex; align-items: center; color: var(--brand-blue); font-weight: 700; }
  .brand__dot { border-radius: 50%; background: var(--brand-green); flex: none; }
  .brand--small { left: 104px; top: 150px; gap: 14px; }
  .brand--small .brand__dot { width: 44px; height: 44px; }
  .brand--small .brand__name { font-size: 24px; line-height: 1.15; }
  .brand--large { left: 0; right: 0; top: 126px; justify-content: center; gap: 20px; }
  .brand--large .brand__dot { width: 66px; height: 66px; }
  .brand--large .brand__name { font-size: 40px; letter-spacing: 0.5px; }

  /* Front details */
  .divider { position: absolute; left: 354px; top: 99px; width: 2px; height: 184px; background: var(--brand-blue); }
  .details { position: absolute; left: 377px; top: 94px; color: var(--text-grey); }
  .person__name { font-size: 21px; font-weight: 700; color: var(--brand-blue); line-height: 25px; }
  .person__role { font-size: 17px; line-height: 21px; }
  .address { margin-top: 17px; font-size: 17px; line-height: 23px; }
  .contacts { list-style: none; margin-top: 17px; font-size: 17px; line-height: 23px; }
  .contacts li { display: flex; align-items: center; gap: 9px; }
  .contacts svg { width: 12px; height: 12px; fill: var(--brand-blue); flex: none; }

  /* Back services */
  .services { position: absolute; left: 0; right: 0; top: 236px; text-align: center; }
  .services__title {
    display: inline-block; font-size: 27px; font-weight: 700; color: var(--brand-blue);
    padding: 0 8px 5px; border-bottom: 3px solid var(--brand-green);
  }
  .services__row { display: flex; justify-content: center; gap: 14px; list-style: none; font-size: 21px; color: var(--text-grey); line-height: 31px; }
  .services__row:first-of-type { margin-top: 10px; }
  .services__row li { display: flex; align-items: center; gap: 9px; }
  .services__row li::before { content: ""; width: 11px; height: 11px; border-radius: 50%; background: var(--brand-blue); }
</style>
</head>
<body>

<section class="card card--front" aria-label="Vorderseite">
  <div class="brand brand--small">
    <span class="brand__dot"></span>
    <span class="brand__name">Varomir<br>Facility Services</span>
  </div>
  <div class="divider"></div>
  <div class="details">
    <p class="person__name">Tarik Kostelac</p>
    <p class="person__role">Geschäftsführer</p>
    <p class="address">Birkenhaldweg 14<br>6330 Cham</p>
    <ul class="contacts">
      <li><svg viewBox="0 0 24 24"><path d="M6.6 10.8a15.1 15.1 0 0 0 6.6 6.6l2.2-2.2a1 1 0 0 1 1-.25 11.4 11.4 0 0 0 3.6.57 1 1 0 0 1 1 1V20a1 1 0 0 1-1 1A17 17 0 0 1 3 4a1 1 0 0 1 1-1h3.5a1 1 0 0 1 1 1c0 1.25.2 2.45.57 3.57a1 1 0 0 1-.25 1z"/></svg>+41 76 519 47 83</li>
      <li><svg viewBox="0 0 24 24"><path d="M2 5h20v14H2zm2 2v.5l8 5 8-5V7l-8 5z"/></svg>info@varomir-fs.ch</li>
      <li><svg viewBox="0 0 24 24"><path d="M12 2a10 10 0 1 0 0 20 10 10 0 0 0 0-20zm6.9 6h-3a15 15 0 0 0-1.3-3.9A8 8 0 0 1 18.9 8zM12 4c.8 1.2 1.5 2.5 1.9 4h-3.8c.4-1.5 1.1-2.8 1.9-4zM4.3 14a8 8 0 0 1 0-4h3.4a16 16 0 0 0 0 4zm.8 2h3a15 15 0 0 0 1.3 3.9A8 8 0 0 1 5.1 16zm3-8h-3a8 8 0 0 1 4.3-3.9A15 15 0 0 0 8.1 8zM12 20c-.8-1.2-1.5-2.5-1.9-4h3.8c-.4 1.5-1.1 2.8-1.9 4zm2.3-6H9.7a14 14 0 0 1 0-4h4.6a14 14 0 0 1 0 4zm.3 5.9a15 15 0 0 0 1.3-3.9h3a8 8 0 0 1-4.3 3.9zm1.7-5.9a16 16 0 0 0 0-4h3.4a8 8 0 0 1 0 4z"/></svg>www.varomir-fs.ch</li>
    </ul>
  </div>
</section>

<section class="card card--back" aria-label="Rückseite">
  <div class="brand brand--large">
    <span class="brand__dot"></span>
    <span class="brand__name">Varomir Facility Services</span>
  </div>
  <div class="services">
    <h2 class="services__title">Services</h2>
    <ul class="services__row">
      <li>Maintenance cleaning</li>
      <li>Industrial cleaning</li>
    </ul>
    <ul class="services__row">
      <li>Cleaning</li>
      <li>Caretaking</li>
      <li>Gardening, disposal</li>
    </ul>
  </div>
</section>

</body>
</html>
```